Harrowmere Freight, Project

Company Profile
Harrowmere Freight Sdn Bhd is a well established and experienced freight forwarder in Kuala Lumpur, Malaysia. We specialize in air and sea forwarding, Custom Brokerage and regulatory compliance services, inland transportation,
overseas freighting and warehousing and distribution management. With our dedicated qualified and experienced professionals, we are fully committed to serving our clients.

Our Mission
Based on the motto “Quick, Reliable and Polite”, Harrowmere Freight is dedicated to upholding the following three points corporate philosophy:
1. Adhering to the principle that “the customer always comes first”.
2. Contributing to the development of the local community.
3. Making it our duty to be responsible and sincere.

Our Edge
• One-Stop Logistics Solutions
• Extensive Network Throughout Malaysia
• Highly Qualified and Experienced Pool of Professionals
• Comprehensive IT Solutions
• Innovative and Customer-focused Solutions
• Flexible and Consistent in Managing Exceptions
• Total Supply Chain Visibility

Target Market(s)

We sell the logistics services to all the industry in Malaysia. (ONE Stop Logistics Solutions)

Industry/Entity Type

Logistic

Contact Information for Business Card

I want the back of the card to be white with the logo and slogan. i would like to see the logo on the front with the general info.

Requirements
Must have
• Name, Title, Office, Cell, Fax, Email, Address, Website
Nice to have
• Modern Design Business Card

```html
<!DOCTYPE html>
<html lang="en">
<head>
<meta charset="utf-8">
<title>Harrowmere Freight — Stationery</title>
<link href="https://fonts.googleapis.com/css2?family=Open+Sans:wght@400;600;700&display=swap" rel="stylesheet">
<style>
  :root{
    --bg:#262626;
    --paper:#ffffff;
    --blue:#2b9ad8;
    --blue-deep:#1b7fc0;
    --grey:#8a8d91;
    --grey-light:#d7d8da;
    --ink:#3a3a3a;
    --ink-soft:#6b6b6b;
  }
  *{box-sizing:border-box;margin:0;padding:0}
  html,body{width:1200px;height:780px;overflow:hidden;background:var(--bg)}
  body{font-family:"Open Sans",Arial,sans-serif;color:var(--ink);position:relative}
  .sheet{position:absolute;background:var(--paper);overflow:hidden;box-shadow:0 8px 24px rgba(0,0,0,.45)}
  .wave{position:absolute;left:0;bottom:0;width:100%}
  .brand{color:var(--blue);font-weight:700;letter-spacing:.2px;line-height:1.05;text-align:center}
  .brand small{display:block;font-size:.55em;font-weight:700}

  /* Letterhead */
  .letterhead{left:60px;top:60px;width:467px;height:660px}
  .letterhead .brand{font-size:22px;margin-top:34px}
  .letter-body{position:absolute;left:48px;right:44px;top:130px;font-size:8.6px;line-height:1.65;color:var(--ink-soft)}
  .letter-body p{margin-bottom:12px;text-align:justify}
  .signoff{position:absolute;right:56px;top:388px;font-size:8px;letter-spacing:.6px;color:var(--ink-soft);text-transform:uppercase}
  .letterhead .wave{height:190px}
  .letter-footer{position:absolute;left:48px;right:30px;bottom:26px;display:flex;gap:14px;color:#fff;font-size:7.4px;line-height:1.55}
  .letter-footer .divider{width:1px;background:rgba(255,255,255,.7)}
  .letter-footer strong{font-weight:700}

  /* Business cards */
  .card{width:300px;height:172px}
  .card-back{left:575px;top:60px}
  .card-front{left:895px;top:60px}
  .card .wave{height:66px}
  .card .slogan{position:absolute;right:14px;bottom:7px;color:#fff;font-size:7px;font-weight:700;letter-spacing:.4px;text-transform:uppercase}
  .services{position:absolute;top:12px;font-size:6.8px;line-height:1.45;color:var(--ink)}
  .services h4{font-size:7.4px;font-weight:700;margin-bottom:2px}
  .services ul{list-style:none}
  .services li::before{content:"";display:inline-block;width:3.5px;height:3.5px;border-radius:50%;background:var(--ink);margin-right:4px;vertical-align:middle}
  .services.left{left:14px}
  .services.right{right:16px}
  .card-back .brand{position:absolute;left:0;right:0;top:62px;font-size:15px}
  .card-front .brand{position:absolute;left:14px;top:34px;font-size:15px;text-align:left}
  .contact{position:absolute;right:16px;top:12px;width:150px;font-size:6.6px;line-height:1.5}
  .contact .name{font-size:10px;font-weight:700;color:var(--blue)}
  .contact .title{font-size:6.6px;color:var(--ink-soft);margin-bottom:6px}
  .contact b{color:var(--blue)}
  .card-address{position:absolute;left:14px;bottom:22px;color:#fff;font-size:5.6px;line-height:1.45;width:150px}

  /* Envelope */
  .envelope{left:575px;top:268px;width:620px;height:310px}
  .envelope .brand{position:absolute;right:120px;top:52px;font-size:26px}
  .envelope .wave{height:190px}
  .envelope-mark{position:absolute;left:0;right:0;bottom:0}
</style>
</head>
<body>

<article class="sheet letterhead">
  <div class="brand">Harrowmere<small>Freight</small></div>
  <div class="letter-body">
    <p>Lorem Ipsum is simply dummy text of the printing and typesetting industry. Lorem Ipsum has been the industry's standard dummy text ever since the 1500s, when an unknown printer took a galley of type and scrambled it to make a type specimen book. It has survived not only five centuries, but also the leap into electronic typesetting, remaining essentially unchanged. It was popularised in the 1960s with the release of Letraset sheets containing Lorem Ipsum passages, and more recently with desktop publishing software like Aldus PageMaker including versions of Lorem Ipsum.</p>
    <p>Established fact that a reader will be distracted by the readable content of a page when looking at its layout. The point of using Lorem Ipsum is that it has a more-or-less normal distribution of letters, as opposed to using 'Content here, content here', making it look like readable English.</p>
    <p>Many desktop publishing packages and web page editors now use Lorem Ipsum as their default model text, and a search for 'lorem ipsum' will uncover many web sites still in their infancy. Various versions have evolved over the years, sometimes by accident, sometimes on purpose (injected humour and the like).</p>
  </div>
  <div class="signoff">Amir Hakimi</div>
  <svg class="wave" viewBox="0 0 100 40" preserveAspectRatio="none" aria-hidden="true">
    <defs><linearGradient id="lh-grey" x1="0" x2="1"><stop offset="0" stop-color="#d7d8da"/><stop offset="1" stop-color="#7d8085"/></linearGradient></defs>
    <path d="M45,22 C70,16 90,10 100,0 L100,40 L45,40 Z" fill="url(#lh-grey)"/>
    <path d="M0,26 C30,14 70,20 100,8 L100,40 L0,40 Z" fill="#2b9ad8"/>
  </svg>
  <footer class="letter-footer">
    <div><strong>HARROWMERE FREIGHT SDN BHD</strong> (1125540-X)<br>No. 8B, 2nd Floor, Jalan Seri Mewah 3,<br>41050 Klang, Selangor Darul Ehsan, Malaysia.</div>
    <div class="divider"></div>
    <div>E: enquiry@harrowmere.com.my<br>T: (603) 3358 1140<br>F: (603) 3358 1190<br>GST Registration No: 000418552907</div>
  </footer>
</article>

<article class="sheet card card-back">
  <div class="services left">
    <h4>We're Specialize In</h4>
    <ul>
      <li>International Shipping (Air/Sea)</li>
      <li>Supply Chain Management</li>
      <li>Tax Exemption Consultancy</li>
      <li>Transportation / Haulage</li>
      <li>Consolidation - NVOCC</li>
      <li>Project Management</li>
    </ul>
  </div>
  <div class="services right">
    <ul>
      <li>Packing</li>
      <li>Marine Insurance</li>
      <li>Warehousing</li>
      <li>Distribution</li>
      <li>Custom Brokerage</li>
      <li>Door to Door</li>
    </ul>
  </div>
  <div class="brand">Harrowmere<small>Freight</small></div>
  <svg class="wave" viewBox="0 0 100 40" preserveAspectRatio="none" aria-hidden="true">
    <defs><linearGradient id="cb-grey" x1="0" x2="1"><stop offset="0" stop-color="#d7d8da"/><stop offset="1" stop-color="#7d8085"/></linearGradient></defs>
    <path d="M50,20 C72,14 90,8 100,-4 L100,40 L50,40 Z" fill="url(#cb-grey)"/>
    <path d="M0,22 C30,10 70,20 100,8 L100,40 L0,40 Z" fill="#2b9ad8"/>
  </svg>
  <div class="slogan">One Stop Logistics Solutions</div>
</article>

<article class="sheet card card-front">
  <div class="brand">Harrowmere<small>Freight</small></div>
  <div class="contact">
    <div class="name">Daniel Farhan</div>
    <div class="title">Managing Director</div>
    <div><b>C:</b> +6012 415 2270</div>
    <div><b>E:</b> daniel.farhan@harrowmere.com.my</div>
    <div><b>T:</b> (603) 3358 1140 / 1141</div>
    <div><b>F:</b> (603) 3358 1190</div>
    <div><b>W:</b> www.harrowmere.com.my</div>
  </div>
  <svg class="wave" viewBox="0 0 100 40" preserveAspectRatio="none" aria-hidden="true">
    <defs><linearGradient id="cf-grey" x1="0" x2="1"><stop offset="0" stop-color="#d7d8da"/><stop offset="1" stop-color="#7d8085"/></linearGradient></defs>
    <path d="M50,20 C72,14 90,8 100,-4 L100,40 L50,40 Z" fill="url(#cf-grey)"/>
    <path d="M0,14 C30,8 70,20 100,8 L100,40 L0,40 Z" fill="#2b9ad8"/>
  </svg>
  <div class="card-address"><b>HARROWMERE FREIGHT SDN BHD</b><br>No. 8B, 2nd Floor, Jalan Seri Mewah 3,<br>41050 Klang, Selangor Darul Ehsan, Malaysia.</div>
  <div class="slogan">One Stop Logistics Solutions</div>
</article>

<article class="sheet envelope">
  <div class="brand">Harrowmere<small>Freight</small></div>
  <svg class="wave" viewBox="0 0 100 40" preserveAspectRatio="none" aria-hidden="true">
    <defs><linearGradient id="env-grey" x1="0" x2="1"><stop offset="0" stop-color="#d7d8da"/><stop offset="1" stop-color="#7d8085"/></linearGradient></defs>
    <path d="M40,22 C70,16 92,10 100,-6 L100,40 L40,40 Z" fill="url(#env-grey)"/>
    <path d="M0,24 C30,14 70,22 100,12 L100,40 L0,40 Z" fill="#2b9ad8"/>
  </svg>
</article>

</body>
</html>
```